Velmora Freightway Solutions Business cards

Would like a very unique design catchy but professional for business cards. Please use log provided.Marlon WellsCeo and Founder TransCon Logistix Solutions1-888-913-3225mwells@tlsolutionsus.comwww.tlsolutionsus.com

```html
<!DOCTYPE html>
<html lang="en">
<head>
<meta charset="utf-8">
<title>Velmora Freightway Solutions – Business Cards</title>
<link href="https://fonts.googleapis.com/css2?family=Lato:wght@400;700&display=swap" rel="stylesheet">
<style>
  :root {
    --page: #e8e8e6;
    --card: #ffffff;
    --brand-blue: #1a6fbd;
    --band-blue: #1472bf;
    --navy: #0f2a44;
    --accent-red: #e8202a;
    --ink: #2c2c2c;
    --white: #ffffff;
  }
  * { box-sizing: border-box; margin: 0; padding: 0; }
  html, body { width: 1200px; height: 960px; overflow: hidden; }
  body {
    position: relative;
    background: var(--page);
    font-family: "Lato", Arial, sans-serif;
  }
  .card {
    position: absolute;
    background: var(--card);
    border-radius: 30px;
    overflow: hidden;
    box-shadow: 0 6px 18px rgba(0,0,0,0.18);
  }
  .card--front { left: 236px; top: 47px; width: 722px; height: 406px; }
  .card--back  { left: 244px; top: 508px; width: 704px; height: 407px; }

  .brand {
    position: absolute;
    left: 0; right: 0;
    display: flex;
    align-items: center;
    justify-content: center;
    gap: 16px;
    color: var(--brand-blue);
    font-weight: 700;
    letter-spacing: 1px;
    white-space: nowrap;
  }
  .brand__mark { background: var(--accent-red); flex: none; }
  .card--front .brand { top: 185px; font-size: 40px; }
  .card--front .brand__mark { width: 40px; height: 40px; }
  .card--back .brand { top: 98px; font-size: 34px; }
  .card--back .brand__mark { width: 34px; height: 34px; }

  .site-line {
    position: absolute;
    left: 0; right: 0; top: 358px;
    display: flex;
    align-items: center;
    justify-content: center;
    gap: 14px;
    font-size: 16px;
    letter-spacing: 2.5px;
    color: var(--ink);
  }
  .site-line__rule { width: 90px; height: 3px; background: var(--brand-blue); border-radius: 2px; }
  .site-line strong { color: var(--brand-blue); font-weight: 700; }

  .bands { position: absolute; left: 0; top: 207px; }

  .person { position: absolute; left: 30px; top: 222px; color: var(--white); }
  .person__name { font-size: 23px; font-weight: 700; letter-spacing: 0.3px; }
  .person__title { font-size: 18px; margin-top: 6px; }

  .portrait {
    position: absolute;
    left: 311px; top: 200px;
    width: 96px; height: 96px;
    border-radius: 50%;
    background: var(--accent-red);
    border: 3px solid var(--white);
  }

  .contact {
    position: absolute;
    display: flex;
    gap: 8px;
    color: var(--white);
    font-size: 17px;
    line-height: 26px;
  }
  .contact svg { flex: none; margin-top: 5px; }
  .contact--address { left: 30px; top: 324px; }
  .contact--phone { left: 404px; top: 296px; }
  .contact--email { left: 404px; top: 332px; }
  .contact--web { left: 404px; top: 368px; }
</style>
</head>
<body>

<section class="card card--front">
  <div class="brand"><span class="brand__mark"></span>Velmora Freightway Solutions</div>
  <div class="site-line">
    <span class="site-line__rule"></span>
    <span>www.<strong>vfwayroutes</strong>.com</span>
    <span class="site-line__rule"></span>
  </div>
</section>

<section class="card card--back">
  <div class="brand"><span class="brand__mark"></span>Velmora Freightway Solutions</div>

  <svg class="bands" width="704" height="200" viewBox="0 0 704 200">
    <rect x="0" y="0" width="704" height="200" fill="var(--band-blue)"/>
    <polygon points="0,0 704,0 704,43 330,43 308,86 0,86" fill="var(--navy)"/>
    <polyline points="0,90 310,90 332,47 360,47" fill="none" stroke="var(--white)" stroke-width="2"/>
  </svg>

  <div class="person">
    <p class="person__name">DORIAN PIKE</p>
    <p class="person__title">CEO AND FOUNDER</p>
  </div>

  <div class="portrait" role="img" aria-label="Profile photo placeholder"></div>

  <div class="contact contact--address">
    <svg width="14" height="16" viewBox="0 0 14 16"><path d="M7 1a5 5 0 0 0-5 5c0 4 5 9 5 9s5-5 5-9a5 5 0 0 0-5-5z" fill="none" stroke="#fff" stroke-width="1.6"/><circle cx="7" cy="6" r="1.8" fill="#fff"/></svg>
    <p>2417 Halden Creek Rd<br>Marietta, GA 30062</p>
  </div>
  <div class="contact contact--phone">
    <svg width="15" height="15" viewBox="0 0 16 16"><path d="M4 1.5l2.3 3-1.3 1.6a9 9 0 0 0 4.9 4.9l1.6-1.3 3 2.3-1.4 2.3C8 14.3 1.7 8 1.7 2.9z" fill="#fff"/></svg>
    <p>1-888-470-6158</p>
  </div>
  <div class="contact contact--email">
    <svg width="16" height="14" viewBox="0 0 16 14"><rect x="1" y="3" width="14" height="10" rx="1" fill="#fff"/><path d="M1.5 3.5L8 8.5l6.5-5" fill="none" stroke="var(--band-blue)" stroke-width="1.3"/></svg>
    <p>dpike@vfwayroutes.com</p>
  </div>
  <div class="contact contact--web">
    <svg width="15" height="15" viewBox="0 0 16 16"><g fill="none" stroke="#fff" stroke-width="1.3"><circle cx="8" cy="8" r="6.5"/><ellipse cx="8" cy="8" rx="3" ry="6.5"/><path d="M1.5 8h13M2.5 4.8h11M2.5 11.2h11"/></g></svg>
    <p>www.vfwayroutes.com</p>
  </div>
</section>

</body>
</html>
```